Very new and innovative Web design for Property managers of Vacation rentals

We are looking for a new website design for travel agencies and property managers specialised on vacation rentals business, holiday villas and apartments.

The end users of this website are travellers who are looking for a vacation home for their next holiday: this is the reason why the website must be easy to use, attractive, professional, possibly elegant and focused on get new reservations.

This is a draft of our current website: https://intro3.kelumsito.com/
Please consider that we would like to have proposals with a totally different and innovative layout, surprise us!

These are the pages of the website:
• Homepage: feel free to redesign all the homepage as you wish, surprise us with something very new! Please consider that Property manager/Travel agencies usually want to have the opportunity to put in evidence groups of houses with specific characteristics (eg. villas with private swimming pool, apartment in big/small towns, villas with air co, etc…), destinations and tourist areas, and sometimes experiences or activities (please consider that the website layout must be suitable even if some of the previous sections are not used).
• Search page: we’d like to organise the results of the search page in three different ways:
o Grid
o Map
o List
• Property page: to illustrate the characteristics, descriptions, images, …. of the property. It is very important to put in evidence images of the property and to maintain the booking form (and the other call to action bottom – eg. whatsapp) always visible
• Custom pages: static pages composed usually by text, images and call to actions
• Contact us (general form)
• Info request (specific of a property form)
• Booking process
• Blog, organised in four pages:
o Home Page – introduction to the blog
o List of articles
o Single article
o Site Map (presentation of categories and sub-categories)

If possible, we’d prefer to receive the material in Adobe XD or similar so that we can obtain the three versions:
- smartphone
- tablet
- desktop

The website will be then developed in Bootstrap: as a result we’ll need the icons in SVG format (or the library used)

In attachment you can find the map of the website pages

```html
<!DOCTYPE html>
<html lang="en">
<head>
<meta charset="utf-8">
<title>Blog – Villora</title>
<link href="https://fonts.googleapis.com/css2?family=Playfair+Display:wght@400;700&family=Figtree:wght@400;500;600&display=swap" rel="stylesheet">
<style>
:root{
  --green:#0fb98a;
  --ink:#1f1f1f;
  --text:#555;
  --line:#e3e3e3;
  --footer:#1c1c1c;
  --footer-text:#bdbdbd;
  --white:#fff;
}
*{box-sizing:border-box;margin:0;padding:0}
html,body{width:1200px;height:2484px;overflow:hidden;background:var(--white)}
body{position:relative;font-family:"Figtree",sans-serif;color:var(--ink)}
a{color:inherit;text-decoration:none}

/* header */
.site-header{position:absolute;top:0;left:0;width:1200px;height:92px;background:var(--white)}
.brand{position:absolute;left:112px;top:26px;display:flex;align-items:center;gap:10px;font-size:29px;font-weight:500;color:var(--green)}
.brand-dot{width:34px;height:34px;border-radius:50%;background:var(--green)}
.utility-bar{position:absolute;right:0;top:0;width:390px;height:42px;background:var(--green);clip-path:polygon(0 0,100% 0,100% 100%,42px 100%);display:flex;justify-content:flex-end;align-items:center;gap:26px;padding-right:70px;font-size:12px;font-weight:600;color:var(--white)}
.utility-bar span{display:flex;align-items:center;gap:6px}
.main-nav{position:absolute;right:112px;top:61px;display:flex;gap:55px;font-size:14px;color:#333}

/* hero */
.hero{position:absolute;top:92px;left:0;width:1200px;height:286px;background:linear-gradient(90deg,#6e6a5a 0%,#5b6058 35%,#3e4c5a 60%,#394a5d 100%);display:flex;align-items:center;justify-content:center}
.hero h1{font-family:"Playfair Display",serif;font-weight:700;font-size:46px;color:var(--white);letter-spacing:1px;margin-top:-40px}

.breadcrumb{position:absolute;left:112px;top:411px;font-size:12.5px;color:#777}
.breadcrumb b{font-weight:500;color:var(--ink)}

/* posts */
.post-grid{position:absolute;left:112px;top:474px;display:grid;grid-template-columns:308px 308px;column-gap:26px;row-gap:38px}
.post{width:308px}
.post-media{height:226px;border-radius:8px;margin-left:1px}
.post-meta{margin-top:32px;font-size:12.5px;color:var(--ink);display:flex;gap:14px;white-space:nowrap}
.post-title{font-family:"Playfair Display",serif;font-weight:400;font-size:26px;line-height:31px;margin-top:16px;width:340px;letter-spacing:-0.2px}
.post-excerpt{margin-top:14px;font-size:13.5px;line-height:19.5px;color:var(--text)}
.btn{display:inline-block;margin-top:19px;margin-left:1px;width:116px;height:44px;line-height:44px;text-align:center;background:var(--green);color:var(--white);font-size:13.5px;font-weight:600}

/* sidebar */
.categories{position:absolute;left:838px;top:474px;width:251px;height:485px;border:1px solid var(--line);padding:20px 26px 0}
.categories h2{font-family:"Playfair Display",serif;font-weight:400;font-size:22px;letter-spacing:.5px}
.categories ul{list-style:none;margin-top:6px}
.categories li{display:flex;justify-content:space-between;height:41.4px;align-items:center;font-size:13.5px}
.categories li::after{content:"+";font-size:15px;margin-right:8px}

/* footer */
.site-footer{position:absolute;top:2158px;left:0;width:1200px;height:326px;background:var(--footer);color:var(--footer-text);font-size:13.5px}
.footer-brand{position:absolute;left:112px;top:120px;display:flex;align-items:center;gap:9px;font-size:23px;font-weight:500;color:var(--green)}
.footer-brand .brand-dot{width:28px;height:28px}
.footer-col{position:absolute;top:50px}
.footer-col h3{font-family:"Playfair Display",serif;font-weight:400;font-size:19px;color:var(--white);margin-bottom:16px}
.footer-col li{list-style:none;height:28px}
.contact li{display:flex;gap:9px;height:auto;margin-bottom:19px;line-height:16px}
.contact svg{flex:none;margin-top:1px}
.social li{display:flex;align-items:center;gap:8px;height:34px}
.social i{width:28px;height:28px;border-radius:50%;background:var(--white)}
.copyright{position:absolute;top:264px;width:100%;text-align:center;font-size:12px}
.copyright b{font-weight:500;color:var(--white)}
</style>
</head>
<body>

<header class="site-header">
  <a class="brand" href="#"><span class="brand-dot"></span>Villora</a>
  <div class="utility-bar">
    <span><svg width="12" height="13" viewBox="0 0 12 13" fill="none" stroke="#fff" stroke-width="1.3"><circle cx="6" cy="4" r="3"/><path d="M1 12.5c0-3 2.2-4.5 5-4.5s5 1.5 5 4.5"/></svg>LOGIN</span>
    <span><svg width="14" height="12" viewBox="0 0 14 12" fill="none" stroke="#fff" stroke-width="1.3"><path d="M7 11S1 7.5 1 4a3 3 0 0 1 6-1 3 3 0 0 1 6 1c0 3.5-6 7-6 7z"/></svg>WHISHLIST</span>
    <span>EN ˅</span>
  </div>
  <nav class="main-nav"><a>HOME</a><a>SEARCH</a><a>PROPERTY</a><a>CUSTOM</a><a>CONTACT US</a></nav>
</header>

<section class="hero" role="img" aria-label="Seaside monastery on a green cliff with a yacht on the sea at dusk">
  <h1>BLOG</h1>
</section>

<div class="breadcrumb">Home &nbsp;/&nbsp; <b>Blog</b></div>

<main class="post-grid">
  <article class="post">
    <div class="post-media" role="img" aria-label="Hotel receptionist welcoming a guest at the front desk" style="background:linear-gradient(135deg,#7a2a2a,#c9a57a 55%,#6fa9ad)"></div>
    <div class="post-meta"><span>Jhon Doe</span><span>I</span><span>December 4, 2020</span><span>I</span><span>0 Comments</span></div>
    <h2 class="post-title">One who avoids a pain that resultant</h2>
    <p class="post-excerpt">Nam libero tempore, cum soluta nobis est eligendi optio cumque nihil impedit quo minus id quod maxime placeat facere possimus, omnis voluptas assumenda est, omnis dolor repellendus.</p>
    <a class="btn" href="#">READ MORE</a>
  </article>
  <article class="post">
    <div class="post-media" role="img" aria-label="Elegant dinner table with glasses and plated dishes" style="background:linear-gradient(135deg,#c9782c,#efe2c8 50%,#d9b48a)"></div>
    <div class="post-meta"><span>Jhon Doe</span><span>I</span><span>December 4, 2020</span><span>I</span><span>0 Comments</span></div>
    <h2 class="post-title">One who avoids a pain that resultant</h2>
    <p class="post-excerpt">Nam libero tempore, cum soluta nobis est eligendi optio cumque nihil impedit quo minus id quod maxime placeat facere possimus, omnis voluptas assumenda est, omnis dolor repellendus.</p>
    <a class="btn" href="#">READ MORE</a>
  </article>
  <article class="post">
    <div class="post-media" role="img" aria-label="Guest relaxing in a tiled swimming pool" style="background:linear-gradient(180deg,#c98c5a,#d9a07a 40%,#3fa8b4 70%,#2a8fa4)"></div>
    <div class="post-meta"><span>Jhon Doe</span><span>I</span><span>December 4, 2020</span><span>I</span><span>0 Comments</span></div>
    <h2 class="post-title">One who avoids a pain that resultant</h2>
    <p class="post-excerpt">Nam libero tempore, cum soluta nobis est eligendi optio cumque nihil impedit quo minus id quod maxime placeat facere possimus, omnis voluptas assumenda est, omnis dolor repellendus.</p>
    <a class="btn" href="#">READ MORE</a>
  </article>
  <article class="post">
    <div class="post-media" role="img" aria-label="Illuminated domed basilica at night" style="background:linear-gradient(180deg,#1a2f6b,#2e4a8a 45%,#b89a6a 75%,#3a2f25)"></div>
    <div class="post-meta"><span>Jhon Doe</span><span>I</span><span>December 4, 2020</span><span>I</span><span>0 Comments</span></div>
    <h2 class="post-title">One who avoids a pain that resultant</h2>
    <p class="post-excerpt">Nam libero tempore, cum soluta nobis est eligendi optio cumque nihil impedit quo minus id quod maxime placeat facere possimus, omnis voluptas assumenda est, omnis dolor repellendus.</p>
    <a class="btn" href="#">READ MORE</a>
  </article>
  <article class="post">
    <div class="post-media" role="img" aria-label="Canal with a gondola between lit shopfronts" style="background:linear-gradient(180deg,#8aa6c4,#b99b78 45%,#4d6f73 80%,#2f4b4e)"></div>
    <div class="post-meta"><span>Jhon Doe</span><span>I</span><span>December 4, 2020</span><span>I</span><span>0 Comments</span></div>
    <h2 class="post-title">One who avoids a pain that resultant</h2>
    <p class="post-excerpt">Nam libero tempore, cum soluta nobis est eligendi optio cumque nihil impedit quo minus id quod maxime placeat facere possimus, omnis voluptas assumenda est, omnis dolor repellendus.</p>
    <a class="btn" href="#">READ MORE</a>
  </article>
  <article class="post">
    <div class="post-media" role="img" aria-label="Bed with white sheets by a window overlooking the sea" style="background:linear-gradient(180deg,#5b6670,#8c9296 50%,#c9cacc)"></div>
    <div class="post-meta"><span>Jhon Doe</span><span>I</span><span>December 4, 2020</span><span>I</span><span>0 Comments</span></div>
    <h2 class="post-title">One who avoids a pain that resultant</h2>
    <p class="post-excerpt">Nam libero tempore, cum soluta nobis est eligendi optio cumque nihil impedit quo minus id quod maxime placeat facere possimus, omnis voluptas assumenda est, omnis dolor repellendus.</p>
    <a class="btn" href="#">READ MORE</a>
  </article>
</main>

<aside class="categories">
  <h2>CATEGORIES</h2>
  <ul>
    <li>Consectetur Adipiscing</li>
    <li>Eget Tempor</li>
    <li>Lobortis Dictum</li>
    <li>Tempus Fermentum</li>
    <li>Quisque</li>
    <li>Consectetur Adipiscing</li>
    <li>Eget Tempor</li>
    <li>Lobortis Dictum</li>
    <li>Tempus Fermentum</li>
    <li>Quisque</li>
  </ul>
</aside>

<footer class="site-footer">
  <a class="footer-brand" href="#"><span class="brand-dot"></span>Villora</a>
  <div class="footer-col" style="left:335px">
    <h3>Quick Links</h3>
    <ul><li>Home</li><li>Search</li><li>Property</li><li>Custom</li><li>Contact Us</li></ul>
  </div>
  <div class="footer-col" style="left:526px">
    <h3>Company</h3>
    <ul><li>Privacy Policies</li><li>Reservation Policies</li><li>Cookie Policy</li></ul>
  </div>
  <div class="footer-col contact" style="left:727px">
    <h3>Contact Us</h3>
    <ul>
      <li><svg width="11" height="14" viewBox="0 0 11 14"><path d="M5.5 0A5.5 5.5 0 0 0 0 5.5C0 9.5 5.5 14 5.5 14S11 9.5 11 5.5A5.5 5.5 0 0 0 5.5 0zm0 7.7a2.2 2.2 0 1 1 0-4.4 2.2 2.2 0 0 1 0 4.4z" fill="#fff"/></svg><span>Via dei Glicini 7 50100<br>Borgo Alto, Toscana (Italy)</span></li>
      <li><svg width="11" height="14" viewBox="0 0 11 14"><path d="M2 0l2.5 3.5-1.4 1.6c.6 1.8 1.7 3.2 3.3 4.2L8 8l3 2.6-1.5 2.8C4.5 13 .5 7 .3 1.6z" fill="#fff"/></svg><span>+39 055 0148272</span></li>
      <li><svg width="13" height="10" viewBox="0 0 13 10"><rect width="13" height="10" fill="#fff"/><path d="M0 0l6.5 5.5L13 0" stroke="#1c1c1c" fill="none"/></svg><span>hello@villora-stays.com</span></li>
    </ul>
  </div>
  <div class="footer-col social" style="left:993px">
    <h3>Follow Us</h3>
    <ul><li><i></i>Community</li><li><i></i>Updates</li><li><i></i>Gallery</li></ul>
  </div>
  <p class="copyright">Copyright © 2021 <b>Villora</b>. All rights reserved.</p>
</footer>

</body>
</html>
```